Thornvale Group needs a business card design

We need a new business card design using the logo recently selected in a logo competition on Pixel Bazaar. Our business is a consultancy specializing in aviation and energy and the winning business card design will promote an image of precision and professionalism with creativity.

Please use the logo with the name on the front of the card and use a complementary font. Make the back white with either the light grey or dark grey logo.

Target Market(s)

Senior finance and legal leaders at aviation and energy companies

Industry/Entity Type

Management Consulting

Contact Information for Business Card

Peter Castrell
President
Thornvale Group

www.thornvalegroup.example

(555) 204-6391
pc@thornvalegroup.example

Requirements
Must have
• Professional font that goes well with the logo font

```html
<!DOCTYPE html>
<html lang="en">
<head>
<meta charset="utf-8">
<title>Thornvale Group – Business Card</title>
<link rel="stylesheet" href="https://fonts.googleapis.com/css2?family=Open+Sans:wght@400;600&display=swap">
<style>
  :root {
    --backdrop: #3a322e;
    --card-white: #ffffff;
    --brand-navy: #0d3f73;
    --ink: #1b1b1b;
  }
  * { box-sizing: border-box; margin: 0; padding: 0; }
  html, body { width: 1200px; height: 844px; overflow: hidden; }
  body {
    background: var(--backdrop);
    font-family: "Open Sans", Arial, sans-serif;
    position: relative;
  }
  .card {
    position: absolute;
    width: 500px;
    height: 286px;
    background: var(--card-white);
    box-shadow: 0 12px 30px rgba(0,0,0,0.45);
    overflow: hidden;
  }
  .card--front { left: 60px; top: 279px; }
  .card--back  { left: 640px; top: 279px; }

  /* Front */
  .wordmark {
    position: absolute;
    right: 40px;
    top: 62px;
    display: flex;
    align-items: center;
    gap: 12px;
    color: var(--brand-navy);
    font-weight: 400;
    font-size: 24px;
    letter-spacing: 3px;
  }
  .wordmark__square {
    width: 18px; height: 18px;
    background: var(--brand-navy);
  }
  .contact { position: absolute; left: 34px; bottom: 24px; }
  .contact__name {
    color: var(--brand-navy);
    font-weight: 600;
    font-size: 20px;
    line-height: 1.1;
  }
  .contact__role { color: var(--ink); font-size: 14px; margin-bottom: 12px; }
  .contact__line {
    display: flex; align-items: center; gap: 10px;
    color: var(--ink); font-size: 14px; line-height: 1.65;
  }
  .contact__icon { width: 13px; height: 13px; fill: var(--brand-navy); flex: none; }

  /* Back */
  .back__panel {
    position: absolute; left: 0; top: 0;
    width: 100%; height: 196px;
    background: var(--brand-navy);
  }
  .back__wordmark {
    position: absolute; left: 0; right: 0; top: 82px;
    text-align: center;
    color: var(--card-white);
    font-weight: 400;
    font-size: 26px;
    letter-spacing: 4px;
  }
  .back__band {
    position: absolute; left: 0; right: 0; top: 196px; bottom: 0;
    display: flex; flex-direction: column; align-items: flex-end;
    justify-content: center; padding-right: 36px; gap: 4px;
  }
  .tagline { color: var(--brand-navy); font-weight: 600; font-size: 15px; }
  .sectors { color: var(--ink); font-size: 12px; }
</style>
</head>
<body>

<section class="card card--front" aria-label="Card front">
  <div class="wordmark"><span class="wordmark__square"></span>THORNVALE GROUP</div>
  <div class="contact">
    <p class="contact__name">Peter J. Castrell</p>
    <p class="contact__role">President</p>
    <p class="contact__line">
      <svg class="contact__icon" viewBox="0 0 24 24" aria-hidden="true"><path d="M6.6 10.8a15 15 0 0 0 6.6 6.6l2.2-2.2c.3-.3.7-.4 1-.2 1.1.4 2.3.6 3.6.6.6 0 1 .4 1 1V20c0 .6-.4 1-1 1A17 17 0 0 1 3 4c0-.6.4-1 1-1h3.5c.6 0 1 .4 1 1 0 1.3.2 2.5.6 3.6.1.3 0 .7-.2 1z"/></svg>
      (555) 204-6391
    </p>
    <p class="contact__line">
      <svg class="contact__icon" viewBox="0 0 24 24" aria-hidden="true"><path d="M2 5h20v14H2z"/><path d="M3 6l9 7 9-7" fill="none" stroke="#fff" stroke-width="1.6"/></svg>
      pc@thornvalegroup.example
    </p>
    <p class="contact__line">
      <svg class="contact__icon" viewBox="0 0 24 24" aria-hidden="true"><circle cx="12" cy="12" r="10" fill="none" stroke="var(--brand-navy)" stroke-width="2"/><path d="M2 12h20M12 2c3 3 3 17 0 20M12 2c-3 3-3 17 0 20" fill="none" stroke="var(--brand-navy)" stroke-width="1.6"/></svg>
      www.thornvalegroup.example
    </p>
  </div>
</section>

<section class="card card--back" aria-label="Card back">
  <div class="back__panel">
    <div class="back__wordmark">THORNVALE GROUP</div>
  </div>
  <div class="back__band">
    <p class="tagline">Finance and Strategy Consulting</p>
    <p class="sectors">Aviation &lt; Manufacturing &lt; Energy</p>
  </div>
</section>

</body>
</html>
```